Business Card Design Project

Business Card
We are rebranding with a new logo
Industry/Entity Type
Business
Contact Information for Business Card
Dennis Morvale +61 487215963 dennis@quorv.com.au P.O. Box 872 Fernlow QLD 4309
Requirements
Must have
- Logo

```html
<!DOCTYPE html>
<html lang="en">
<head>
<meta charset="utf-8">
<title>Quorv International – Business Card</title>
<link href="https://fonts.googleapis.com/css2?family=Open+Sans:wght@400;600;700&display=swap" rel="stylesheet">
<style>
  :root {
    --backdrop: #3a3c40;
    --card-white: #f7f7f7;
    --brand-blue: #1a7499;
    --brand-blue-light: #2d8fb8;
    --brand-blue-dark: #0f5674;
    --brand-orange: #e8821c;
    --text-white: #ffffff;
    --text-soft: #d6ecf5;
  }
  * { box-sizing: border-box; margin: 0; padding: 0; }
  html, body {
    width: 1200px; height: 960px; overflow: hidden;
    background: var(--backdrop);
    font-family: "Open Sans", Arial, sans-serif;
  }
  .sheet {
    width: 1200px; height: 960px;
    display: flex; flex-direction: column;
    align-items: center; justify-content: center; gap: 40px;
  }
  .card {
    position: relative;
    width: 720px; height: 411px;
    overflow: hidden;
    box-shadow: 0 14px 30px rgba(0,0,0,.35);
  }

  /* Wordmark (shared) */
  .wordmark { display: flex; align-items: center; gap: 14px; font-weight: 700; }
  .wordmark-dot { width: 16px; height: 16px; border-radius: 50%; flex: none; }
  .wordmark-text { display: flex; flex-direction: column; align-items: center; line-height: 1.1; }
  .wordmark-name { letter-spacing: 4px; }
  .wordmark-tag { letter-spacing: 4px; }

  /* Back */
  .card-back {
    background: radial-gradient(ellipse at 50% 42%, var(--brand-blue-light) 0%, var(--brand-blue) 45%, var(--brand-blue-dark) 100%);
    display: flex; flex-direction: column; align-items: center; justify-content: center;
  }
  .card-back .wordmark { color: var(--text-white); }
  .card-back .wordmark-dot { background: var(--text-white); }
  .card-back .wordmark-name { font-size: 56px; }
  .card-back .wordmark-tag { font-size: 24px; }
  .back-web {
    margin-top: 30px;
    color: var(--text-soft);
    font-size: 17px; letter-spacing: 5px;
  }

  /* Front */
  .card-front { background: var(--card-white); }
  .front-shape { position: absolute; inset: 0; }
  .card-front .wordmark {
    position: absolute; left: 78px; top: 140px;
    color: var(--brand-blue);
  }
  .card-front .wordmark-dot { width: 14px; height: 14px; background: var(--brand-orange); }
  .card-front .wordmark-name { font-size: 44px; }
  .card-front .wordmark-tag { font-size: 19px; letter-spacing: 3px; }
  .contact {
    position: absolute; right: 42px; top: 118px;
    text-align: right; color: var(--text-white);
    font-size: 16px; line-height: 24px;
  }
  .contact-name {
    color: var(--brand-orange);
    font-weight: 700; font-size: 17px; letter-spacing: .5px;
    margin-bottom: 16px;
  }
  .contact-line { display: flex; justify-content: flex-end; align-items: center; gap: 8px; }
  .contact-line.plain { padding-right: 22px; }
  .contact-icon { width: 14px; height: 14px; flex: none; }
</style>
</head>
<body>
<main class="sheet">

  <section class="card card-back" aria-label="Card back">
    <div class="wordmark">
      <span class="wordmark-dot"></span>
      <div class="wordmark-text">
        <span class="wordmark-name">QUORV</span>
        <span class="wordmark-tag">INTERNATIONAL</span>
      </div>
    </div>
    <div class="back-web">www.quorv.com.au</div>
  </section>

  <section class="card card-front" aria-label="Card front">
    <svg class="front-shape" viewBox="0 0 720 411" width="720" height="411">
      <defs>
        <radialGradient id="panelGlow" cx="70%" cy="45%" r="65%">
          <stop offset="0" stop-color="#2d8fb8"/>
          <stop offset=".55" stop-color="#1a7499"/>
          <stop offset="1" stop-color="#0f5674"/>
        </radialGradient>
      </defs>
      <path d="M450 0 C405 120 390 260 330 411 L300 411 C362 262 392 128 442 0 Z" fill="#e8821c"/>
      <path d="M450 0 C405 120 390 260 330 411 L720 411 L720 0 Z" fill="url(#panelGlow)"/>
    </svg>

    <div class="wordmark">
      <span class="wordmark-dot"></span>
      <div class="wordmark-text">
        <span class="wordmark-name">QUORV</span>
        <span class="wordmark-tag">INTERNATIONAL</span>
      </div>
    </div>

    <div class="contact">
      <div class="contact-name">DENNIS MORVALE</div>
      <div class="contact-line plain">P.O. Box 872</div>
      <div class="contact-line plain">Fernlow QLD 4309</div>
      <div class="contact-line">+61 487215963
        <svg class="contact-icon" viewBox="0 0 14 14"><path d="M3 1 L5.5 1 L6.5 4 L5 5.2 C5.8 7 7 8.2 8.8 9 L10 7.5 L13 8.5 L13 11 C13 12 12 13 11 13 C5.5 12.5 1.5 8.5 1 3 C1 2 2 1 3 1 Z" fill="#e8821c"/></svg>
      </div>
      <div class="contact-line">dennis@quorv.com.au
        <svg class="contact-icon" viewBox="0 0 14 14"><rect x="1" y="3" width="12" height="8.5" rx="1" fill="#e8821c"/><path d="M1.5 3.5 L7 8 L12.5 3.5" fill="none" stroke="#1a7499" stroke-width="1.2"/></svg>
      </div>
      <div class="contact-line">www.quorv.com.au
        <svg class="contact-icon" viewBox="0 0 14 14"><circle cx="7" cy="7" r="6" fill="#e8821c"/><path d="M1 7 H13 M7 1 C4 4 4 10 7 13 M7 1 C10 4 10 10 7 13" fill="none" stroke="#1a7499" stroke-width="1"/></svg>
      </div>
    </div>
  </section>

</main>
</body>
</html>
```